Professional Single Page Website Design for Tollbrook Advisory

Tollbrook Advisory is a new business consultancy specializing in providing expert services to small businesses, primarily in the brick-and-mortar retail and food service sectors. We offer a range of services including franchise development and launch, due diligence, and construction management.

Currently, we have a basic website set up at www.tollbrookadvisory.example, but we need a professional touch to enhance its design and functionality.

Project Requirements:
- Single Page Design: For now, we need a single page design that effectively showcases who we are, our services, and contact information.
- Future Expansion: The design should be flexible and scalable for future expansion to include additional pages like specific service offerings, about us, and a dedicated contact page.
- Design Aesthetic: We are looking for a modern yet professional design that aligns with our brand identity.
- Logo: We have a logo that we like, which was also sourced from Pixel Bazaar. The logo files are attached to this project brief.

Key Sections to Include:
- Hero Section: An engaging introduction to Tollbrook Advisory with a strong visual impact.
- About Us: A brief overview of who we are and our mission.
- Team: Section for the profiles of the two principals.
- Services: A clear and concise presentation of our services, including franchise development, due diligence, and construction management.
- Contact Information: Easy-to-find contact details, including a form for inquiries.
- Call to Action: Encouraging visitors to get in touch with us for consultations or further information.

Design Considerations:
- Ensure the design is responsive and mobile-friendly.
- Include high-quality images and icons that complement our services and industry.
- We do not need development services, this is only a design project.

```html
<!DOCTYPE html>
<html lang="en">
<head>
<meta charset="utf-8">
<title>Tollbrook Advisory</title>
<link href="https://fonts.googleapis.com/css2?family=Inter:wght@300;400;500;600;700;800&display=swap" rel="stylesheet">
<style>
:root{
  --teal:#8cc5ae;
  --teal-dark:#7bb8a0;
  --ink:#111111;
  --text:#2b2b2b;
  --muted:#555555;
  --light-bg:#efefef;
  --white:#ffffff;
  --black:#000000;
}
*{margin:0;padding:0;box-sizing:border-box}
html,body{width:1200px;height:3273px;overflow:hidden}
body{font-family:"Inter",sans-serif;color:var(--text);background:var(--white);position:relative}
.abs{position:absolute}
.btn{position:absolute;display:flex;align-items:center;justify-content:center;background:var(--teal);color:var(--white);font-weight:600;border-radius:40px;text-transform:uppercase;letter-spacing:.2px}
.heading{position:absolute;font-weight:300;text-transform:uppercase;color:var(--ink);line-height:1.2}
.heading b{font-weight:800}
.rule{position:absolute;height:3px;background:var(--teal)}

/* hero */
.hero{position:absolute;left:0;top:0;width:1200px;height:703px;overflow:hidden}
.hero-photo{position:absolute;inset:0;background:
  radial-gradient(ellipse 520px 300px at 640px 470px,rgba(214,96,40,.75),transparent 70%),
  radial-gradient(ellipse 400px 200px at 420px 140px,rgba(170,70,60,.5),transparent 70%),
  linear-gradient(180deg,#2c2f3a 0%,#3e3440 30%,#3a2a26 60%,#1c1714 100%)}
.hero-shade{position:absolute;inset:0;background:rgba(0,0,0,.25)}
.logo{position:absolute;left:95px;top:14px;display:flex;align-items:center;gap:12px}
.logo-dot{width:60px;height:60px;border-radius:50%;border:5px solid var(--teal)}
.logo-name{font-size:21px;font-weight:600;color:var(--white);line-height:1.05;width:130px}
.nav{position:absolute;top:44px;left:0;width:1200px;font-size:17px;color:var(--white)}
.nav a{position:absolute;color:var(--white);text-decoration:none;transform:translateX(-50%)}
.nav a.active::after{content:"";position:absolute;left:-2px;right:-2px;bottom:-12px;height:2px;background:var(--white)}
.hero-title{position:absolute;left:0;width:1200px;text-align:center;color:var(--white);text-transform:uppercase;line-height:1}
.hero-title.line1{top:245px;font-size:54px;font-weight:300}
.hero-title.line1 span{position:relative}
.hero-title.line1 span::before,.hero-title.line1 span::after{content:"";position:absolute;top:50%;width:36px;height:2px;background:var(--white)}
.hero-title.line1 span::before{left:-50px}
.hero-title.line1 span::after{right:-50px}
.hero-title.line2{top:295px;font-size:54px;font-weight:800}
.hero-sub{position:absolute;top:357px;width:1200px;text-align:center;font-size:21px;font-weight:300;color:var(--white)}
.dots{position:absolute;top:658px;left:563px;display:flex;gap:8px;align-items:center}
.dots i{display:block;width:8px;height:8px;border-radius:50%;background:rgba(255,255,255,.6)}
.dots i.on{background:var(--white)}
.dots i.arrow{width:14px;height:14px;background:var(--white)}

/* about */
.about{position:absolute;left:0;top:703px;width:1200px;height:544px;background:var(--light-bg)}
.about-photo{position:absolute;left:160px;top:144px;width:318px;height:318px;border-radius:60px;transform:rotate(45deg);background:linear-gradient(135deg,#c7b9a6,#6e6a64 55%,#e6e0d8)}
.about-copy{position:absolute;left:590px;top:240px;width:530px;font-size:15.5px;line-height:24px;color:var(--text)}

/* mission */
.mission{position:absolute;left:0;top:1247px;width:1200px;height:220px;background:var(--teal)}
.mission-title{position:absolute;left:109px;top:78px;font-size:33px;font-weight:300;color:var(--white)}
.mission-title b{font-weight:800}
.mission-copy{position:absolute;left:394px;top:56px;width:700px;font-size:17px;line-height:25px;color:var(--white);font-weight:300}

/* team */
.member-accent{position:absolute;width:81px;height:82px;background:var(--teal)}
.member-photo{position:absolute;width:215px;height:224px}
.member-name{position:absolute;font-size:22px;font-weight:600;color:var(--ink)}
.member-role{position:absolute;font-size:18px;font-weight:300;color:var(--text)}
.member-bio{position:absolute;width:252px;font-size:12px;line-height:20px;color:var(--muted)}

/* services */
.services{position:absolute;left:0;top:1938px;width:1200px;height:544px;background:var(--light-bg)}
.card{position:absolute;top:153px;width:298px;height:299px;background:var(--white)}
.card-icon{position:absolute;left:34px;top:44px}
.card-title{position:absolute;left:35px;top:128px;font-size:18px;font-weight:600;color:var(--ink)}
.card-text{position:absolute;left:38px;top:155px;width:232px;font-size:10.5px;line-height:19px;color:var(--muted)}
.card .btn{left:35px;top:242px;width:114px;height:27px;font-size:9px}

/* contact */
.contact{position:absolute;left:0;top:2482px;width:1200px;height:588px;background:var(--black);overflow:hidden}
.contact-item{position:absolute;left:141px;display:flex;align-items:center;gap:12px;color:var(--white)}
.contact-icon{width:56px;height:56px;border-radius:50%;border:2px solid var(--white);display:flex;align-items:center;justify-content:center}
.contact-label{font-size:16.5px;line-height:27px}
.contact-label b{font-weight:700;display:block;font-size:16.5px}
.field{position:absolute;left:637px;width:445px;border:1.5px solid var(--white);color:var(--white);font-size:15px;padding:16px 23px}
.send{position:absolute;left:632px;top:454px;width:179px;height:43px;border-radius:30px;background:var(--black);color:var(--white);font-weight:700;font-size:15px;display:flex;align-items:center;justify-content:center}

/* footer */
.footer{position:absolute;left:0;top:3070px;width:1200px;height:203px;background:var(--white)}
.footer-nav a{position:absolute;top:46px;transform:translateX(-50%);font-size:17px;font-weight:700;color:var(--ink);text-decoration:none}
.copyright{position:absolute;top:87px;width:1200px;text-align:center;font-size:14px;color:var(--ink)}
.social{position:absolute;top:127px;width:30px;height:30px;border-radius:50%;border:1.5px solid var(--ink)}
</style>
</head>
<body>

<header class="hero">
  <div class="hero-photo" role="img" aria-label="Modern glass commercial building lit up at dusk with people on the plaza"></div>
  <div class="hero-shade"></div>
  <div class="logo"><span class="logo-dot"></span><span class="logo-name">Tollbrook Advisory</span></div>
  <nav class="nav">
    <a class="active" style="left:415px">Home</a>
    <a style="left:572px">About Us</a>
    <a style="left:745px">Services</a>
    <a style="left:903px">Team</a>
    <a style="left:1058px">Contact</a>
  </nav>
  <h1 class="hero-title line1"><span>Building Success</span></h1>
  <h1 class="hero-title line2">In Southern California</h1>
  <p class="hero-sub">Expertise at Every Step: From Planning to Execution</p>
  <a class="btn" style="left:507px;top:403px;width:168px;height:41px;font-size:14px">Get in touch</a>
  <div class="dots"><i class="arrow"></i><i class="on"></i><i></i><i></i><i></i><i class="arrow"></i></div>
</header>

<section class="about">
  <div class="about-photo" role="img" aria-label="Business consultant in a suit meeting with a client at a cafe table"></div>
  <h2 class="heading" style="left:590px;top:106px;font-size:38px;line-height:46px">About <b>Tollbrook<br>Advisory</b></h2>
  <div class="rule" style="left:590px;top:210px;width:94px"></div>
  <p class="about-copy">Welcome to Tollbrook Advisory, your trusted partner in navigating the complexities of the real estate and small business markets. Founded by industry veterans Daniel Reyes and Kevin Hwang, we specialize in providing comprehensive services tailored to the unique needs of our clients. Whether you're a franchisee, a new restaurant owner, or a commercial real estate investor, our expertise in due diligence, construction management, and investment property evaluation ensures you make informed, strategic decisions.</p>
  <a class="btn" style="left:587px;top:482px;width:181px;height:43px;font-size:15px">Learn more</a>
</section>

<section class="mission">
  <h2 class="mission-title">OUR <b>MISSION</b></h2>
  <p class="mission-copy">At Tollbrook, we blend innovative strategies with local market expertise to guide your commercial real estate ventures. Whether you're launching a new restaurant, investing in retail spaces, or expanding a franchise, our dedicated team is here to turn your real estate aspirations into tangible success.</p>
</section>

<section class="team">
  <h2 class="heading" style="left:0;width:1200px;text-align:center;top:1513px;font-size:38px">Our <b>Team</b></h2>
  <div class="rule" style="left:546px;top:1571px;width:93px"></div>

  <div class="member-accent" style="left:97px;top:1616px"></div>
  <div class="member-photo" style="left:108px;top:1627px;background:linear-gradient(160deg,#b9c8d6,#e9e4df 60%,#d8d0c6)" role="img" aria-label="Portrait of principal Daniel Reyes"></div>
  <div class="member-name" style="left:351px;top:1639px">Daniel Reyes</div>
  <div class="member-role" style="left:351px;top:1667px">Principal</div>
  <p class="member-bio" style="left:354px;top:1697px">Daniel Reyes brings almost 20 years of rich experience as a real estate investor and a pivotal role at one of southern California's largest real estate firms, where he...</p>
  <a class="btn" style="left:351px;top:1814px;width:121px;height:28px;font-size:9.5px">Learn more</a>

  <div class="member-accent" style="left:619px;top:1621px"></div>
  <div class="member-photo" style="left:631px;top:1632px;background:linear-gradient(160deg,#4a3b2c,#2a211a 60%,#1a1a22)" role="img" aria-label="Portrait of principal Kevin Hwang"></div>
  <div class="member-name" style="left:874px;top:1644px">Kevin Hwang</div>
  <div class="member-role" style="left:874px;top:1672px">Principal</div>
  <p class="member-bio" style="left:877px;top:1702px">Kevin Hwang is a seasoned real estate expert with extensive experience in project and construction management, and a licensed agent in California. Fluent in English and Korean</p>
  <a class="btn" style="left:874px;top:1819px;width:121px;height:28px;font-size:9.5px">Learn more</a>
</section>

<section class="services">
  <h2 class="heading" style="left:0;width:1200px;text-align:center;top:41px;font-size:38px">Services <b>Provide</b></h2>
  <div class="rule" style="left:554px;top:97px;width:94px"></div>

  <div class="abs" style="left:117px;top:141px;width:102px;height:92px;background:var(--teal)"></div>
  <div class="abs" style="left:988px;top:373px;width:101px;height:91px;background:var(--teal)"></div>

  <svg class="abs" style="left:72px;top:290px" width="24" height="34" viewBox="0 0 24 34"><path d="M18 3 L5 17 L18 31" fill="none" stroke="#111" stroke-width="4"/></svg>
  <svg class="abs" style="left:1122px;top:290px" width="24" height="34" viewBox="0 0 24 34"><path d="M6 3 L19 17 L6 31" fill="none" stroke="#111" stroke-width="4"/></svg>

  <div class="card" style="left:130px">
    <svg class="card-icon" width="56" height="58" viewBox="0 0 56 58" fill="none" stroke="#222" stroke-width="2">
      <rect x="14" y="2" width="28" height="18"/><path d="M10 20 H46 L42 28 H14 Z"/><rect x="20" y="8" width="16" height="8"/>
      <path d="M28 28 V38 M8 38 H48 M8 38 V44 M28 38 V44 M48 38 V44"/>
      <rect x="2" y="44" width="12" height="12"/><rect x="22" y="44" width="12" height="12"/><rect x="42" y="44" width="12" height="12"/>
    </svg>
    <div class="card-title">Franchise Development</div>
    <p class="card-text">At Tollbrook Advisory, our Franchise Development &amp; Launch service is designed to transform your successful business into a thriving franchise. We start by thoroughly</p>
    <a class="btn">Learn more</a>
  </div>

  <div class="card" style="left:454px">
    <svg class="card-icon" width="56" height="54" viewBox="0 0 56 54" fill="none" stroke="#222" stroke-width="2">
      <circle cx="14" cy="14" r="6"/><circle cx="14" cy="14" r="11" stroke-dasharray="4 3"/>
      <path d="M22 22 H44 V46 H20 V28"/><path d="M26 30 H38 M26 36 H38 M26 42 H34"/><circle cx="46" cy="46" r="6"/><path d="M43 46 L45 48 L49 44"/>
    </svg>
    <div class="card-title">Due Diligence</div>
    <p class="card-text">Tollbrook offers comprehensive evaluations tailored to your business needs. We meticulously assess franchise opportunities, business sales, and property transactions,</p>
    <a class="btn">Learn more</a>
  </div>

  <div class="card" style="left:780px">
    <svg class="card-icon" width="58" height="58" viewBox="0 0 58 58" fill="none" stroke="#222" stroke-width="2">
      <path d="M4 2 H46 V20 M4 2 V50 H22"/><path d="M10 10 H16 M10 18 H16 M10 26 H16"/>
      <path d="M24 40 A14 14 0 0 1 52 40 Z"/><path d="M38 26 V34 M20 40 H56 M28 46 H48 M30 52 H46"/>
    </svg>
    <div class="card-title">Construction Management</div>
    <p class="card-text">Our Building &amp; Construction Management Services oversee every aspect of your construction and development projects, from initial planning to final completion.</p>
    <a class="btn">Learn more</a>
  </div>
</section>

<section class="contact">
  <svg class="abs" style="left:0;top:0" width="1200" height="588" viewBox="0 0 1200 588"><polygon points="623,0 1200,0 1200,588 455,588" fill="#8cc5ae"/></svg>
  <h2 class="heading" style="left:141px;top:118px;font-size:38px;color:var(--white)">Contact <b>Us</b></h2>
  <div class="rule" style="left:141px;top:177px;width:98px"></div>

  <div class="contact-item" style="top:224px">
    <span class="contact-icon"><svg width="20" height="26" viewBox="0 0 20 26"><path d="M10 1 A9 9 0 0 1 19 10 C19 17 10 25 10 25 C10 25 1 17 1 10 A9 9 0 0 1 10 1 Z" fill="#fff"/><circle cx="10" cy="10" r="3.5" fill="#000"/></svg></span>
    <span class="contact-label">Address:<b>218 Harbor View Ave Suite 40</b></span>
  </div>
  <div class="contact-item" style="top:307px">
    <span class="contact-icon"><svg width="24" height="18" viewBox="0 0 24 18"><rect x="0" y="0" width="24" height="18" rx="2" fill="#fff"/><path d="M1 2 L12 10 L23 2" fill="none" stroke="#000" stroke-width="2"/></svg></span>
    <span class="contact-label">Email address:<b>info@tollbrookadvisory.example</b></span>
  </div>
  <div class="contact-item" style="top:388px">
    <span class="contact-icon"><svg width="24" height="24" viewBox="0 0 24 24" fill="none" stroke="#fff" stroke-width="2"><path d="M5 2 L9 6 L7 9 C8 12 11 15 14 16 L17 14 L21 18 L18 21 C10 21 3 14 3 6 Z"/><path d="M14 3 A8 8 0 0 1 21 10 M14 7 A4 4 0 0 1 17 10"/></svg></span>
    <span class="contact-label">Phone number:<b>(555) 014-2291</b></span>
  </div>

  <div class="field" style="top:140px;height:55px">Name*</div>
  <div class="field" style="top:205px;height:55px">Email address*</div>
  <div class="field" style="top:268px;height:55px">Phone*</div>
  <div class="field" style="top:336px;height:89px">Message</div>
  <div class="send">SEND NOW</div>
</section>

<footer class="footer">
  <nav class="footer-nav">
    <a style="left:309px">Home</a>
    <a style="left:451px">About Us</a>
    <a style="left:610px">Services</a>
    <a style="left:752px">Team</a>
    <a style="left:892px">Contact</a>
  </nav>
  <p class="copyright">© 2024 Tollbrook Advisory | All Rights Reserved</p>
  <span class="social" style="left:558px"></span>
  <span class="social" style="left:595px"></span>
  <span class="social" style="left:631px"></span>
</footer>

</body>
</html>
```